Podiatry clinic requires a modern revamp and editing of existing website.

I would like a fresh new look and updated information for my current business website. An easy to navigate site with prominent address and phone number for call to action. We are a podiatry clinic that focuses on general and sports podiatry.
I would like 4 pages; including Home page, About Us, Services & Contact.
www.brambleridgepodiatry.net

Target Market(s)

Active working professionals.

Industry/Entity Type

Medical

Coding

Coded - Design and coding required

Number of Pages Required

4 page

Font styles to use
Sans Serif

Colors
6b449b

Requirements
Must have
• A modern look with logo and active images; clean and uncluttered. Visible phone number and address for call to action.
• 4 pages - Home, About Us, Services, Contact.
• Home page - update address & service logos.
• About Us - update of personal information.
• Services - Revamp of existing page.
• Contact page to include Google map, email & phone number.
Nice to have
• Ability to add content easily; eg. a blog or adding video onto Home page.
• Link to Facebook page.

```html
<!DOCTYPE html>
<html lang="en">
<head>
<meta charset="utf-8">
<title>Bramble Ridge Podiatry</title>
<link href="https://fonts.googleapis.com/css2?family=Raleway:wght@400;500;600;700&family=Arimo:wght@400;700&family=PT+Sans:wght@700&display=swap" rel="stylesheet">
<style>
:root{
  --header:#9a7cc0;
  --brand:#6b449b;
  --deep:#3f2a6b;
  --ink:#1e1a3a;
  --orange:#f07b1f;
  --cta-red:#f0401f;
  --text:#444;
  --white:#fff;
  --footer:#f4f4f6;
  --rule:#d8d8dc;
}
*{margin:0;padding:0;box-sizing:border-box}
html,body{width:1200px;height:2228px;overflow:hidden}
body{position:relative;font-family:"Arimo",Arial,sans-serif;color:var(--text);background:var(--white)}
.abs{position:absolute}
a{color:inherit}

/* header */
.site-header{left:0;top:0;width:1200px;height:89px;background:var(--header);border-top:3px solid var(--brand)}
.brand{left:141px;top:14px;display:flex;align-items:center;gap:8px;font-family:"Raleway",sans-serif;font-weight:700;font-size:17px;color:var(--white);line-height:1.1;width:120px}
.brand-square{width:20px;height:20px;background:var(--brand);flex:none}
.main-nav{left:486px;top:54px;display:flex;gap:0;font-family:"Raleway",sans-serif;font-size:17px;font-weight:500;color:var(--white)}
.main-nav a{text-decoration:none;position:absolute;white-space:nowrap}
.main-nav .active{color:var(--orange)}
.nav-marker{left:501px;top:0;width:0;height:0;border-left:9px solid transparent;border-right:9px solid transparent;border-top:8px solid var(--orange)}
.header-divider{left:879px;top:20px;width:1px;height:52px;background:rgba(255,255,255,.7)}
.call{left:906px;top:34px}
.call-label{left:943px;top:35px;font-size:14px;color:var(--white)}
.call-number{left:941px;top:54px;font-size:21px;color:#2a1f44;font-family:"Arimo",sans-serif}

/* hero */
.hero{left:0;top:89px;width:1200px;height:361px;display:flex}
.hero-panel{height:100%}
.hero-run{width:400px;background:linear-gradient(160deg,#c9b6a8,#d98a4a 55%,#8c5a3a)}
.hero-family{width:420px;background:linear-gradient(180deg,#e9f1f7,#b9cfe0 45%,#6f8f4a 80%,#5a6b3a)}
.hero-orthotic{width:380px;background:linear-gradient(135deg,#f2f2f2,#d9c6b6 50%,#c9a58a)}
.hero-arrow{top:298px;width:26px;height:34px;background:rgba(255,255,255,.55)}
.tagline{left:0;top:450px;width:1200px;height:52px;background:var(--brand);color:var(--white);font-family:"Raleway",sans-serif;font-weight:600;font-size:24px;text-align:center;line-height:52px}
.tagline b{font-weight:700}

/* welcome */
.welcome-title{left:126px;top:535px;font-family:"Raleway",sans-serif;font-size:31px;font-weight:400;color:#333}
.title-dots{left:126px;top:577px}
.welcome-copy{left:126px;top:602px;width:560px;font-size:13.5px;line-height:22px;color:#555}
.welcome-copy p{margin-bottom:10px}
.read-more{font-size:13.5px;color:#333;text-decoration:underline}
.welcome-more{left:126px;top:760px}
.video{left:737px;top:554px;width:330px;height:221px;border:2px solid #333;border-radius:3px;overflow:hidden;background:#111}
.video-frame{position:absolute;left:0;top:0;width:100%;height:186px;background:linear-gradient(135deg,#e9eef3,#d4b9a5 55%,#b58c72)}
.video-controls{position:absolute;left:0;bottom:0;width:100%;height:35px;background:linear-gradient(#3a3a3a,#151515)}

/* services */
.services{left:0;top:821px;width:1200px;height:533px;background:var(--deep)}
.notch{width:0;height:0;border-left:22px solid transparent;border-right:22px solid transparent;border-top:16px solid var(--white)}
.services-title{left:0;top:855px;width:1200px;text-align:center;font-family:"Raleway",sans-serif;font-size:31px;color:var(--white)}
.services-title span{color:var(--orange)}
.services-intro{left:0;top:932px;width:1200px;text-align:center;font-size:17px;color:var(--white)}
.service{top:980px;width:320px;text-align:center;color:var(--white)}
.service-icon{width:128px;height:128px;border-radius:50%;margin:0 auto;background:radial-gradient(circle at 50% 40%,#fff,#e6e3ec);border:4px solid #8f84a8}
.service-name{margin-top:32px;font-family:"PT Sans",sans-serif;font-size:21px;font-weight:700}
.service-desc{margin-top:8px;font-size:15px;line-height:26px;padding:0 10px}
.service-more{display:inline-block;margin-top:12px;font-size:14px;color:var(--orange);text-decoration:underline}
.service-divider{top:995px;width:1px;height:282px;background:rgba(255,255,255,.2)}

/* blog & accreditations */
.news-band{left:0;top:1354px;width:1200px;height:495px;background:linear-gradient(120deg,#d6d9de,#eceef1 40%,#e9dfe6 75%,#d9cfe0)}
.section-head{font-family:"Arimo",sans-serif;font-size:28px;color:#2a2a2a}
.head-rule{height:2px;background:#9a9a9a}
.head-rule i{display:block;width:130px;height:2px;background:var(--orange)}
.post-thumb{width:108px;height:89px;border:3px solid var(--white);box-shadow:0 1px 3px rgba(0,0,0,.3)}
.post{left:258px;width:300px;font-size:12.5px;line-height:18px;color:#444}
.post h3{font-size:13px;font-weight:700;color:#222;margin-bottom:2px}
.post time{display:block;color:var(--brand);font-size:12.5px}
.post .more{color:var(--brand)}
.badge{width:206px;height:79px;background:var(--white);border:1px solid #999;display:flex;align-items:center;justify-content:center}
.badge-shape{width:150px;height:44px;border-radius:6px}

/* call to action */
.cta{left:0;top:1849px;width:1200px;height:83px;background:var(--deep)}
.cta-button{left:195px;top:1870px;width:210px;height:40px;background:#9a7cc0;color:var(--white);font-family:"Raleway",sans-serif;font-size:19px;font-weight:500;text-align:center;line-height:40px}
.cta-text{left:429px;top:1863px;font-family:"Raleway",sans-serif;font-size:20px;line-height:28px;color:var(--white)}
.cta-text span{color:var(--cta-red)}

/* footer */
.site-footer{left:0;top:1932px;width:1200px;height:251px;background:var(--footer)}
.foot-head{font-family:"Raleway",sans-serif;font-weight:600;font-size:18px;color:#333;padding-bottom:8px;border-bottom:1px solid var(--rule)}
.quick-links{left:132px;top:1956px;width:135px}
.quick-links ul{list-style:none;margin-top:12px}
.quick-links li{font-size:14px;line-height:25px;color:#333;padding-left:16px;position:relative}
.quick-links li::before{content:"›";position:absolute;left:0;color:#999}
.contact{left:352px;top:1956px;width:250px}
.contact-row{display:flex;gap:14px;font-size:14px;line-height:19px;color:#333;padding:12px 0;border-bottom:1px solid var(--rule)}
.hours{left:680px;top:1956px;width:170px}
.hours-row{font-size:14px;line-height:20px;color:#333;padding:10px 0;border-bottom:1px solid var(--rule)}
.hours-row:last-child{border-bottom:0}
.foot-brand{left:930px;top:1987px;width:166px;height:147px;background:#9a7cc0;color:var(--brand);font-family:"Raleway",sans-serif;font-weight:700;font-size:22px;line-height:1.2;padding:30px 16px}
.col-divider{width:1px;background:var(--rule)}
.bottom-bar{left:0;top:2183px;width:1200px;height:45px;background:var(--ink)}
.copyright{left:131px;top:2197px;font-size:14px;color:#ddd}
.social{top:2184px;width:32px;height:32px;border-radius:50%;background:#6d6a78;top:2189px}
</style>
</head>
<body>

<header class="site-header abs"></header>
<div class="brand abs"><span class="brand-square"></span>Bramble Ridge Podiatry</div>
<div class="nav-marker abs"></div>
<nav class="main-nav abs">
  <a class="active" style="left:0">Home</a>
  <a style="left:80px">About Us</a>
  <a style="left:184px">Services</a>
  <a style="left:285px">Contact Us</a>
</nav>
<div class="header-divider abs"></div>
<svg class="call abs" width="28" height="28" viewBox="0 0 28 28"><circle cx="14" cy="14" r="12.5" fill="none" stroke="#fff" stroke-width="2"/><path d="M10 8c1 0 2 2 2 3s-1 1-1 2 2 4 4 4 1-1 2-1 3 1 3 2-1 2-2 2c-4 0-10-6-10-10 0-1 1-2 2-2z" fill="#fff"/></svg>
<div class="call-label abs">Call Us Today</div>
<div class="call-number abs">1300 555 274</div>

<section class="hero abs">
  <div class="hero-panel hero-run" role="img" aria-label="Close-up of a runner's shoes on a trail"></div>
  <div class="hero-panel hero-family" role="img" aria-label="Family running together outdoors on a sunny hillside"></div>
  <div class="hero-panel hero-orthotic" role="img" aria-label="Podiatrist fitting an orthotic insole to a patient's foot"></div>
</section>
<svg class="hero-arrow abs" style="left:0" viewBox="0 0 26 34"><path d="M16 10l-7 7 7 7" fill="none" stroke="#666" stroke-width="2"/></svg>
<svg class="hero-arrow abs" style="left:1152px" viewBox="0 0 26 34"><path d="M10 10l7 7-7 7" fill="none" stroke="#666" stroke-width="2"/></svg>
<div class="tagline abs"><b>bramble ridge podiatry</b> is a podiatry clinic in the heart of melbourne CBD</div>

<h1 class="welcome-title abs">Welcome to Bramble Ridge Podiatry</h1>
<svg class="title-dots abs" width="550" height="14"><circle cx="6" cy="7" r="4" fill="#ccc"/><circle cx="26" cy="7" r="6" fill="#ccc"/><circle cx="44" cy="7" r="4" fill="#ccc"/><line x1="52" y1="3" x2="548" y2="3" stroke="#ccc"/></svg>
<div class="welcome-copy abs">
  <p>Bramble Ridge Podiatry is a Podiatry clinic in the heart of Melbourne CBD. We are located between Harlow &amp; Pemberton Streets in the Harlow Business Centre / Linden Court Complex.</p>
  <p>Our podiatrists are fully qualified health professionals who are able to diagnose, treat, manage or help to prevent all medical conditions that affect the feet and lower limb.</p>
</div>
<a class="read-more welcome-more abs">Read More</a>

<div class="video abs">
  <div class="video-frame" role="img" aria-label="Video still of a podiatrist examining a patient's foot"></div>
  <svg class="abs" style="left:145px;top:74px" width="40" height="34"><rect width="40" height="34" rx="5" fill="#111"/><path d="M15 10l12 7-12 7z" fill="#fff"/></svg>
  <div class="video-controls">
    <svg width="330" height="35"><path d="M14 12l8 5-8 5z" fill="#fff"/><path d="M38 14h4l5-4v14l-5-4h-4z" fill="#fff"/><rect x="62" y="15" width="190" height="5" rx="2" fill="#555"/><rect x="62" y="15" width="85" height="5" rx="2" fill="#d22"/><path d="M300 12h6v2h-4v4h-2zM318 24h-6v-2h4v-4h2z" fill="#fff"/></svg>
  </div>
</div>

<section class="services abs"></section>
<div class="notch abs" style="left:578px;top:821px"></div>
<h2 class="services-title abs">Our <span>Services</span></h2>
<svg class="abs" style="left:420px;top:895px" width="360" height="16"><circle cx="6" cy="8" r="4" fill="#a79cc0"/><circle cx="20" cy="8" r="4" fill="#a79cc0"/><circle cx="38" cy="8" r="6" fill="#a79cc0"/><line x1="46" y1="8" x2="314" y2="8" stroke="#a79cc0"/><circle cx="322" cy="8" r="6" fill="#a79cc0"/><circle cx="340" cy="8" r="4" fill="#a79cc0"/><circle cx="354" cy="8" r="4" fill="#a79cc0"/></svg>
<p class="services-intro abs">We provide General Podiatry Treatment and some Specialised Services in relation to various foot conditions, including</p>

<div class="service abs" style="left:107px">
  <div class="service-icon" role="img" aria-label="Knee joint icon"></div>
  <h3 class="service-name">Sports Injuries</h3>
  <p class="service-desc">Using our StrideScan platform, we will scan your gait and generate a report outlining areas where....{+}</p>
  <a class="service-more">Read More</a>
</div>
<div class="service-divider abs" style="left:428px"></div>
<div class="service abs" style="left:449px">
  <div class="service-icon" role="img" aria-label="Patient resting in bed icon"></div>
  <h3 class="service-name">Orthotic Therapy</h3>
  <p class="service-desc">Our team uses a combination of manual evaluation and automated testing for its orthotic fitting. ...{+}</p>
  <a class="service-more">Read More</a>
</div>
<div class="service-divider abs" style="left:778px"></div>
<div class="service abs" style="left:770px">
  <div class="service-icon" role="img" aria-label="Toes and toenails icon"></div>
  <h3 class="service-name">Nail Surgery</h3>
  <p class="service-desc">Our team can assist you with your ingrown nail assessment &amp; advise on treatment techniques....{+}</p>
  <a class="service-more">Read More</a>
</div>

<section class="news-band abs" role="img" aria-label="Blurred background of a laptop on a desk"></section>
<div class="notch abs" style="left:578px;top:1354px;border-top-color:var(--deep)"></div>

<svg class="abs" style="left:131px;top:1430px" width="36" height="30"><ellipse cx="20" cy="11" rx="14" ry="10" fill="#9a7cc0"/><ellipse cx="13" cy="16" rx="12" ry="9" fill="var(--brand)"/><path d="M6 22l-3 6 9-4z" fill="var(--brand)"/></svg>
<h2 class="section-head abs" style="left:181px;top:1430px">Latest Blog Posts</h2>
<svg class="abs" style="left:506px;top:1442px" width="46" height="20"><circle cx="10" cy="10" r="8" fill="none" stroke="#bbb" stroke-width="1.5"/><path d="M12 6l-4 4 4 4" fill="none" stroke="#bbb" stroke-width="1.5"/><circle cx="34" cy="10" r="8" fill="none" stroke="#666" stroke-width="1.5"/><path d="M32 6l4 4-4 4" fill="none" stroke="#666" stroke-width="1.5"/></svg>
<div class="head-rule abs" style="left:131px;top:1474px;width:430px"><i></i></div>

<div class="post-thumb abs" style="left:131px;top:1510px;background:linear-gradient(135deg,#7a6a5a,#b08a6a)" role="img" aria-label="Author portrait"></div>
<article class="post abs" style="top:1508px">
  <h3>Ut tellus dolor, dapibus smit dollar nomk egemop</h3>
  <time>15.08.2015</time>
  Utm tellus dolor, dapibus eget, elemen velmki cursu eleifelitas. Aenean auctorbni wisi et urnam. Aliquam at volutpatis <span class="more">[...]</span>
</article>
<div class="post-thumb abs" style="left:131px;top:1638px;background:linear-gradient(135deg,#8a3a3a,#c9a08a)" role="img" aria-label="Author portrait"></div>
<article class="post abs" style="top:1636px">
  <h3>Ut tellus dolor, dapibus smit dollar nomk egemop</h3>
  <time>15.08.2015</time>
  Utm tellus dolor, dapibus eget, elemen velmki cursu eleifelitas. Aenean auctorbni wisi et urnam. Aliquam at volutpatis <span class="more">[...]</span>
</article>

<h2 class="section-head abs" style="left:633px;top:1432px;font-size:31px">Our Accreditations</h2>
<div class="head-rule abs" style="left:633px;top:1474px;width:433px"><i></i></div>
<div class="badge abs" style="left:637px;top:1525px" role="img" aria-label="Podiatry association accreditation badge"><div class="badge-shape" style="background:#e6e1f0"></div></div>
<div class="badge abs" style="left:861px;top:1525px" role="img" aria-label="Sports medicine body accreditation badge"><div class="badge-shape" style="background:#dbe6f2"></div></div>
<div class="badge abs" style="left:637px;top:1629px" role="img" aria-label="Health fund claiming accreditation badge"><div class="badge-shape" style="background:#eeeeee"></div></div>
<div class="badge abs" style="left:861px;top:1629px" role="img" aria-label="Public health scheme accreditation badge"><div class="badge-shape" style="background:#1a9a4a"></div></div>

<section class="cta abs"></section>
<a class="cta-button abs">Book An Appointment</a>
<p class="cta-text abs">We are eligible service providers for all <span>Veteran Gold Card holders.</span><br>Transport &amp; workplace injury claims accepted. On the spot health insurance</p>

<footer class="site-footer abs"></footer>
<div class="quick-links abs">
  <h4 class="foot-head">Quick Links</h4>
  <ul><li>Consulting</li><li>Inspections</li><li>Training</li><li>General Contracing</li><li>Clients</li><li>Contact Us</li></ul>
</div>
<div class="col-divider abs" style="left:310px;top:1990px;height:150px"></div>
<div class="contact abs">
  <h4 class="foot-head">Contact Details</h4>
  <div class="contact-row"><svg width="12" height="16" viewBox="0 0 12 16"><path d="M6 0a6 6 0 016 6c0 4-6 10-6 10S0 10 0 6a6 6 0 016-6z" fill="#222"/><circle cx="6" cy="6" r="2" fill="#f4f4f6"/></svg><span>Suite 214 / 62 Harlow<br>Street &nbsp;Melbourne &nbsp;3000</span></div>
  <div class="contact-row" style="padding:20px 0"><svg width="14" height="14" viewBox="0 0 14 14"><path d="M3 0c1 0 2 3 2 4s-1 1-1 2 3 4 4 4 1-1 2-1 4 1 4 2-1 3-3 3C6 14 0 8 0 3c0-2 2-3 3-3z" fill="#222"/></svg><span>1300 555 274</span></div>
  <div class="contact-row" style="border:0;padding-top:14px"><svg width="14" height="12" viewBox="0 0 14 12"><rect y="1" width="14" height="10" fill="#222"/><path d="M0 1l7 6 7-6" fill="none" stroke="#f4f4f6"/></svg><span>info@brambleridgepodiatry.net</span></div>
</div>
<div class="col-divider abs" style="left:664px;top:1990px;height:150px"></div>
<div class="hours abs">
  <h4 class="foot-head">Hours of Operation</h4>
  <div class="hours-row">Monday to Friday<br>10:00am to 07:00pm</div>
  <div class="hours-row" style="padding-top:14px">Saturday<br>10:00am to 05:00pm</div>
  <div class="hours-row" style="padding-top:14px">Sunday<br>By Appointment Only</div>
</div>
<div class="foot-brand abs">Bramble Ridge Podiatry</div>

<div class="bottom-bar abs"></div>
<p class="copyright abs">Copyright © 2016 Fernvale Digital Services. &nbsp;All Right Reserved.</p>
<div class="social abs" style="left:974px" aria-label="Social link"></div>
<div class="social abs" style="left:1015px" aria-label="Social link"></div>
<div class="social abs" style="left:1056px" aria-label="Social link"></div>

</body>
</html>
```